Redesign of business card for Cedar Ridge Mechanical

We are looking for a new design for our business cards for Cedar Ridge Mechanical. We are a plumbing & HVAC construction company, operating on the West Coast of Canada and USA. Logo attached.
Industry/Entity Type
Construction - Plumbing & HVAC
Contact Information for Business Card
Name, address, phone numbers, email, website address
Look and feel
Each slider illustrates characteristics of the customer's brand and the style your logo design should communicate.

```html
<!DOCTYPE html>
<html lang="en">
<head>
<meta charset="utf-8">
<title>Cedar Ridge Mechanical – Business Card</title>
<link rel="stylesheet" href="https://fonts.googleapis.com/css2?family=Poppins:wght@400;500;700&display=swap">
<style>
  :root {
    --stage: #2a2a2a;
    --ink: #0b0b0b;
    --paper: #ffffff;
    --muted: #2e2e2e;
    --rule: #9a9ab0;
    --ghost: #ededed;
  }
  * { box-sizing: border-box; margin: 0; padding: 0; }
  html, body { width: 1200px; height: 866px; overflow: hidden; }
  body {
    background: var(--stage);
    font-family: "Poppins", sans-serif;
    display: flex;
    flex-direction: column;
    align-items: center;
    justify-content: center;
    gap: 30px;
  }
  .card {
    position: relative;
    width: 680px;
    height: 389px;
    overflow: hidden;
    box-shadow: 0 10px 30px rgba(0,0,0,.45);
  }
  /* Front */
  .card--front { background: var(--paper); color: var(--ink); }
  .ghost-block {
    position: absolute;
    left: 70px; top: -60px;
    width: 250px; height: 190px;
    border-radius: 28px;
    background: var(--ghost);
  }
  .identity {
    position: absolute;
    left: 48px; top: 132px;
    width: 250px;
  }
  .identity__name { font-weight: 700; font-size: 22px; letter-spacing: .5px; text-transform: uppercase; line-height: 1.1; }
  .identity__role { font-size: 15px; color: var(--muted); margin-top: 2px; }
  .identity__rule { height: 1px; background: var(--rule); margin: 12px 0 10px; }
  .contact { list-style: none; font-size: 15px; line-height: 1.55; }
  .contact li { display: flex; align-items: center; gap: 8px; }
  .contact svg { width: 14px; height: 14px; fill: var(--ink); flex: none; }

  .brand {
    position: absolute;
    display: flex;
    align-items: center;
    gap: 14px;
    font-weight: 700;
    text-transform: uppercase;
    line-height: 1.05;
  }
  .brand__square { flex: none; background: currentColor; }
  .card--front .brand { right: 44px; top: 110px; font-size: 26px; }
  .card--front .brand__square { width: 58px; height: 58px; }

  .address {
    position: absolute;
    right: 44px; top: 258px;
    width: 300px;
    text-align: right;
    font-size: 14px;
    line-height: 1.35;
    border-top: 1px solid var(--rule);
    padding-top: 8px;
  }
  .band { position: absolute; left: 0; bottom: 0; width: 680px; height: 64px; }
  .website {
    position: absolute;
    right: 44px; bottom: 14px;
    color: var(--paper);
    font-size: 16px;
    font-weight: 500;
    letter-spacing: .5px;
  }

  /* Back */
  .card--back { background: var(--ink); color: var(--paper); }
  .card--back .brand {
    left: 50%; top: 50%;
    transform: translate(-50%, -50%);
    font-size: 34px;
    white-space: nowrap;
  }
  .card--back .brand__square { width: 76px; height: 76px; }
</style>
</head>
<body>

<section class="card card--front" aria-label="Business card front">
  <div class="ghost-block" aria-hidden="true"></div>

  <div class="identity">
    <p class="identity__name">Daniel Foster</p>
    <p class="identity__role">Managing Director</p>
    <div class="identity__rule"></div>
    <ul class="contact">
      <li>
        <svg viewBox="0 0 24 24" aria-hidden="true"><path d="M6.6 10.8a15.1 15.1 0 0 0 6.6 6.6l2.2-2.2a1 1 0 0 1 1-.25 11.4 11.4 0 0 0 3.6.57 1 1 0 0 1 1 1V20a1 1 0 0 1-1 1A17 17 0 0 1 3 4a1 1 0 0 1 1-1h3.5a1 1 0 0 1 1 1c0 1.25.2 2.45.57 3.57a1 1 0 0 1-.25 1z"/></svg>
        604-555 0148
      </li>
      <li>
        <svg viewBox="0 0 24 24" aria-hidden="true"><path d="M2 5h20v14H2z M2 5l10 8 10-8" /></svg>
        hello@cedarridgemech.com
      </li>
    </ul>
  </div>

  <div class="brand">
    <span class="brand__square" aria-hidden="true"></span>
    <span>Cedar Ridge<br>Mechanical</span>
  </div>

  <p class="address">88 Harbour Street, Vancouver<br>BC V6B 1A1, Canada</p>

  <svg class="band" viewBox="0 0 680 64" aria-hidden="true">
    <path d="M0 54 H220 C250 54 250 14 280 14 H680 V64 H0 Z" fill="#0b0b0b"/>
  </svg>
  <p class="website">www.cedarridgemech.com</p>
</section>

<section class="card card--back" aria-label="Business card back">
  <div class="brand">
    <span class="brand__square" aria-hidden="true"></span>
    <span>Cedar Ridge<br>Mechanical</span>
  </div>
</section>

</body>
</html>
```